Looking for a dynamic business card for a pizzeria.

A business card with our food, logo, and space for name, title, email, website, phone. The card should convey quality, unique, amazing. On the front, I envision food photo or photos with the owners names and contact information. On the back, more food with locations, website, facebook, twitter, instagram icons. It should look polished, not cartoonish, or plain.
Target Market(s)
upscale, local food buyers, 30-50 years in age.
Industry/Entity Type
Restaurant
Contact Information for Business Card
Business Name: Bru'nettix, LLC
Website: www.brunettix.com
Back:
2 locations: (can list on the back of card)
1. Harbor Point
4087 Corlan Avenue
Marlow, WA 98301
360-481-5067
2. Cedar Ridge
7315 Wendmere Road
Marlow, WA 98304
360-293-8840
front:
EDITABLE space for
Business name
Person's Name
title
2nd title
Email address
cell-phone number
Requirements
Must have
- logo
- my food photo or photos (no watermarks showing)
- locations on back
- Person contact information on front
- full bleed

```html
<!DOCTYPE html>
<html lang="en">
<head>
<meta charset="utf-8">
<title>Brunettix Business Card</title>
<link rel="stylesheet" href="https://fonts.googleapis.com/css2?family=Cabin:wght@400;500&display=swap">
<style>
  :root {
    --bg: #e9e6e1;
    --card-white: #ffffff;
    --brand-red: #b5141c;
    --brand-green: #2f6a35;
    --ink: #1f1f1f;
    --photo-warm: #c4553c;
    --photo-cream: #e9d2b4;
    --photo-dark: #7a2a1c;
  }
  * { box-sizing: border-box; margin: 0; padding: 0; }
  html, body { width: 1200px; height: 843px; overflow: hidden; }
  body {
    background: var(--bg);
    display: flex;
    flex-direction: column;
    align-items: center;
    justify-content: center;
    gap: 30px;
    font-family: "Cabin", sans-serif;
  }
  .card {
    position: relative;
    width: 660px;
    height: 377px;
    background: var(--card-white);
    overflow: hidden;
    box-shadow: 0 6px 18px rgba(0,0,0,0.18);
  }
  .brand-name {
    font-family: "Cabin", sans-serif;
    font-weight: 500;
    color: var(--ink);
    letter-spacing: 1px;
    line-height: 1;
  }

  /* Back side: photo + locations */
  .food-photo {
    position: absolute;
    inset: 0 0 100px 0;
    background:
      radial-gradient(ellipse at 70% 30%, var(--photo-cream) 0%, transparent 45%),
      radial-gradient(ellipse at 30% 70%, var(--photo-warm) 0%, transparent 60%),
      linear-gradient(135deg, var(--photo-warm) 0%, var(--photo-dark) 55%, var(--photo-warm) 100%);
  }
  .back-brand {
    position: absolute;
    top: 34px;
    left: 28px;
    display: flex;
    align-items: center;
    gap: 12px;
    background: rgba(255,255,255,0.85);
    padding: 10px 14px;
  }
  .back-brand .brand-name { font-size: 34px; }
  .brand-dot {
    width: 30px; height: 30px;
    border-radius: 50%;
    background: var(--brand-red);
  }
  .location {
    position: absolute;
    bottom: 12px;
    font-style: normal;
    font-size: 15px;
    line-height: 1.25;
    color: var(--ink);
  }
  .location .location-name,
  .location .label { color: var(--brand-green); }
  .location--left { left: 36px; }
  .location--right { right: 36px; text-align: right; }

  /* Front side: contact */
  .front-art { position: absolute; inset: 0; }
  .front-brand {
    position: absolute;
    top: 36px;
    left: 42px;
  }
  .front-brand .brand-name { font-size: 42px; }
  .person {
    position: absolute;
    top: 108px;
    left: 52px;
  }
  .person-name {
    font-size: 24px;
    font-weight: 500;
    letter-spacing: 1px;
    color: var(--brand-green);
  }
  .person-title {
    font-size: 18px;
    color: var(--brand-red);
  }
  .contact-list {
    position: absolute;
    top: 178px;
    left: 52px;
    list-style: none;
    font-size: 18px;
    color: var(--ink);
  }
  .contact-list li {
    display: flex;
    align-items: center;
    gap: 12px;
    height: 28px;
  }
  .contact-list svg { width: 16px; height: 16px; fill: var(--brand-green); }
  .social {
    position: absolute;
    right: 34px;
    bottom: 24px;
    display: flex;
    gap: 12px;
  }
  .social span {
    width: 22px; height: 22px;
    border-radius: 50%;
    background: var(--card-white);
  }
</style>
</head>
<body>

  <section class="card card--back" aria-label="Card back">
    <div class="food-photo" role="img" aria-label="Close-up photo of a pepperoni pizza being prepared by hand"></div>
    <div class="back-brand">
      <span class="brand-name">BRUNETTIX</span>
      <span class="brand-dot"></span>
    </div>
    <address class="location location--left">
      <span class="location-name">Cedar Ridge</span><br>
      7315 Wendmere Road<br>
      Marlow, WA 98304<br>
      <span class="label">Phone:</span> 360-293-8840
    </address>
    <address class="location location--right">
      <span class="location-name">Harbor Point</span><br>
      4087 Corlan Avenue<br>
      Marlow, WA 98301<br>
      <span class="label">Phone:</span> 360-481-5067
    </address>
  </section>

  <section class="card card--front" aria-label="Card front">
    <svg class="front-art" viewBox="0 0 660 377" preserveAspectRatio="none" aria-hidden="true">
      <rect width="660" height="377" fill="var(--brand-red)"/>
      <path d="M0 0 H430 V250 C300 300 130 290 0 320 Z" fill="var(--card-white)"/>
      <circle cx="450" cy="170" r="170" fill="var(--card-white)"/>
    </svg>
    <div class="front-brand"><span class="brand-name">BRUNETTIX</span></div>
    <div class="person">
      <p class="person-name">DANIEL MARSH</p>
      <p class="person-title">Founder</p>
    </div>
    <ul class="contact-list">
      <li>
        <svg viewBox="0 0 16 16"><path d="M4 0h8a1 1 0 0 1 1 1v14a1 1 0 0 1-1 1H4a1 1 0 0 1-1-1V1a1 1 0 0 1 1-1zm1 2v10h6V2zm3 11a1 1 0 1 0 0 2 1 1 0 0 0 0-2z"/></svg>
        689 512 0734
      </li>
      <li>
        <svg viewBox="0 0 16 16"><path d="M0 3h16v10H0zm1.5 1.2V12h13V4.2L8 9z"/></svg>
        name@brunettix.com
      </li>
      <li>
        <svg viewBox="0 0 16 16"><path d="M8 0a8 8 0 1 0 0 16A8 8 0 0 0 8 0zm0 1.5c1 0 2 2 2.3 5H5.7C6 3.5 7 1.5 8 1.5zM5.7 9.5h4.6C10 12.5 9 14.5 8 14.5S6 12.5 5.7 9.5zM1.6 7.5h2.6c0 .3 0 .7 0 1H1.6zm10.2 0h2.6v1h-2.6z"/></svg>
        www.brunettix.com
      </li>
    </ul>
    <div class="social" aria-hidden="true"><span></span><span></span></div>
  </section>

</body>
</html>
```